Duct Manufacturing Company new to the industry needs business card and stationary design

we are sheet metal duct manufacturers looking for a business card design to fit my new business logo.
nothing to crazy that will date, but want it to stand out from the crowed.
I'm sure you guys will work it out.

Contact Information for Business Card

Glen Marsh
Director

Address
17 Dorwell St
Karrindale NSW 2718

0438 760 514

Sales@flowbend.com.au

Font styles to use
Other font styles liked:
• BankGothic md bt

Requirements
Nice to have
• Like the idea of corner rounded to match logo
• like to keep colours flowing
• font I like sharp square not rounded

```html
<!DOCTYPE html>
<html lang="en">
<head>
<meta charset="utf-8">
<title>Flowbend Industries – Business Card</title>
<link rel="stylesheet" href="https://fonts.googleapis.com/css2?family=Open+Sans:wght@400;600&display=swap">
<style>
  :root {
    --backdrop: #3b3b3b;
    --card-black: #121212;
    --card-charcoal: #2a2a2a;
    --wave-blue: #0f6fc9;
    --wave-blue-deep: #0a4fa3;
    --accent-green: #6cbf2c;
    --arc-grey: #8d8d8d;
    --ink-light: #ffffff;
    --brand-ink: #e8e8e8;
  }
  html, body {
    margin: 0;
    padding: 0;
    width: 1200px;
    height: 750px;
    overflow: hidden;
    background: var(--backdrop);
    font-family: "Open Sans", Arial, sans-serif;
  }
  .business-card {
    position: absolute;
    left: 180px;
    top: 136px;
    width: 840px;
    height: 478px;
    overflow: hidden;
    background: linear-gradient(180deg, #050505 0%, var(--card-black) 20%, var(--card-charcoal) 100%);
  }
  .card-waves {
    position: absolute;
    inset: 0;
    width: 100%;
    height: 100%;
  }
  .brand-name {
    position: absolute;
    left: 96px;
    top: 218px;
    display: flex;
    align-items: center;
    gap: 14px;
    color: var(--brand-ink);
    font-weight: 600;
    font-size: 30px;
    letter-spacing: 3px;
    line-height: 1.15;
  }
  .brand-dot {
    width: 22px;
    height: 22px;
    border-radius: 50%;
    background: var(--accent-green);
    flex: none;
  }
  .contact-block {
    position: absolute;
    right: 45px;
    top: 0;
    width: 400px;
    height: 100%;
    color: var(--ink-light);
    text-align: right;
  }
  .contact-block p { margin: 0; position: absolute; right: 0; white-space: nowrap; }
  .person-name { top: 204px; font-size: 30px; font-weight: 600; }
  .person-role { top: 244px; font-size: 22px; }
  .address-line { font-size: 20px; }
  .address-street { top: 284px; }
  .address-town { top: 310px; }
  .contact-line {
    font-size: 20px;
    display: flex;
    align-items: center;
    gap: 10px;
  }
  .contact-phone { top: 350px; }
  .contact-email { top: 382px; }
  .contact-web { top: 414px; }
  .contact-icon { width: 22px; height: 22px; flex: none; }
</style>
</head>
<body>
  <div class="business-card">
    <svg class="card-waves" viewBox="0 0 576 328" preserveAspectRatio="none" aria-hidden="true">
      <path d="M355,160 C420,98 500,76 576,80 L576,118 C500,104 430,118 355,160 Z" fill="var(--arc-grey)"/>
      <path d="M0,236 C50,265 120,290 232,262 C160,300 70,304 0,276 Z" fill="var(--accent-green)"/>
      <path d="M0,292 C80,308 190,300 262,240 C330,182 380,110 470,98 C520,92 560,98 576,102 L576,328 L0,328 Z" fill="#0a0a0a"/>
      <defs>
        <linearGradient id="waveBlue" x1="0" y1="1" x2="1" y2="0">
          <stop offset="0" stop-color="var(--wave-blue-deep)"/>
          <stop offset="1" stop-color="var(--wave-blue)"/>
        </linearGradient>
      </defs>
      <path d="M0,298 C80,312 195,304 266,246 C334,190 384,118 472,106 C522,100 560,104 576,108 L576,328 L0,328 Z" fill="url(#waveBlue)"/>
    </svg>

    <div class="brand-name">
      <span class="brand-dot"></span>
      <span>FLOWBEND<br>INDUSTRIES</span>
    </div>

    <div class="contact-block">
      <p class="person-name">Glen Marsh</p>
      <p class="person-role">Director</p>
      <p class="address-line address-street">17 Dorwell St</p>
      <p class="address-line address-town">Karrindale NSW 2718</p>
      <p class="contact-line contact-phone">0438 760 514
        <svg class="contact-icon" viewBox="0 0 24 24"><path fill="#fff" d="M6.6 10.8a15.1 15.1 0 0 0 6.6 6.6l2.2-2.2a1 1 0 0 1 1-.25 11.4 11.4 0 0 0 3.6.57 1 1 0 0 1 1 1V20a1 1 0 0 1-1 1A17 17 0 0 1 3 4a1 1 0 0 1 1-1h3.5a1 1 0 0 1 1 1c0 1.25.2 2.45.57 3.57a1 1 0 0 1-.25 1z"/></svg>
      </p>
      <p class="contact-line contact-email">Sales@flowbend.com.au
        <svg class="contact-icon" viewBox="0 0 24 24"><rect x="2" y="5" width="20" height="14" rx="1" fill="#fff"/><path d="M3 6l9 7 9-7" fill="none" stroke="#0f6fc9" stroke-width="1.6"/></svg>
      </p>
      <p class="contact-line contact-web">www.flowbend.com.au
        <svg class="contact-icon" viewBox="0 0 24 24"><circle cx="12" cy="12" r="9.5" fill="#fff"/><path d="M12 2.5v19M2.5 12h19M12 2.5c-4 4-4 15 0 19M12 2.5c4 4 4 15 0 19" fill="none" stroke="#0f6fc9" stroke-width="1.3"/></svg>
      </p>
    </div>
  </div>
</body>
</html>
```